Brochure and Business Card design

I am looking for a high end, elegant A4, 4 page brochure booklet to convey our products to clientele that will be visiting a luxury display showroom.

Harrowgate Locks and Grilles is a Australian security provider, and we supply high end products from reputable brands.
The brochure will be directed to clients building a new home with a partnered building company and will be accompanied with display boards of our products.

I am providing files of a document we have put together with the relevant information and some images to help along the way, we are not bound by the layout or style it has been drawn up and we wish to give you complete creative freedom putting the peaces together. I have also provided the files for our logo in two different colours, and a picture of a brochure we love the look of.

If you have any suggestions, we can likely come up with further images etc if it will help or even if you feel some should be removed, we are open to that also

Target Market(s)

Young familys, people building new luxury homes, proffesionals, home owners

Industry/Entity Type

Business

Font styles to use
Serif
Sans Serif

Requirements
Must have
• All 8 pages
Should not have
• Not really a fan of reds and similar.

```html
<!DOCTYPE html>
<html lang="en">
<head>
<meta charset="utf-8">
<title>Harrowgate Brochure – Pages 2 and 3</title>
<link rel="stylesheet" href="https://fonts.googleapis.com/css2?family=Questrial&family=Montserrat:wght@400;600;700&display=swap">
<style>
:root{
  --stage:#cfcfcf;
  --paper:#ffffff;
  --blue:#2a7fc1;
  --button:#2784c6;
  --green:#8dbb3e;
  --ink:#3a3a3a;
  --muted:#555;
  --card-line:#e6e6e6;
  --rule:#bdbdbd;
  --thumb:#dcdcdc;
}
*{margin:0;padding:0;box-sizing:border-box}
html,body{width:1200px;height:645px;overflow:hidden;background:var(--stage)}
body{position:relative;font-family:"Montserrat",Arial,sans-serif;color:var(--ink)}
.page-label{position:absolute;top:96px;font:700 12px "Montserrat",Arial,sans-serif;color:#111;transform:translateX(-50%)}
.spread{position:absolute;left:98px;top:127px;width:1002px;height:388px;background:var(--paper)}
.spread > *{position:absolute}
.photo{background:linear-gradient(90deg,#ffffff 0%,#9c9894 35%,#6d6a67 100%)}
.photo--intercom{background:linear-gradient(90deg,#ffffff 0%,#efe8df 45%,#c9b59c 100%)}
.page-title{font:400 35px/1 "Questrial","Century Gothic",sans-serif;color:var(--blue)}
.body-text{font-size:6.6px;line-height:7.3px;text-align:justify;color:var(--muted)}
.body-text p+p{margin-top:7px}
.section-head{font:600 11px "Montserrat",Arial,sans-serif;color:var(--green)}
.upgrades-head{font:700 10px "Montserrat",Arial,sans-serif;color:var(--green);letter-spacing:.2px}
.cta{background:var(--button);color:#fff;font:700 8.6px "Montserrat",Arial,sans-serif;display:flex;align-items:center;padding-left:10px}
.card{border:1px solid var(--card-line);display:flex;align-items:center;gap:8px;padding:4px 6px;background:#fff}
.card .thumb{flex:none;width:32px;height:36px;background:linear-gradient(160deg,#f0f0f0,var(--thumb));border-radius:2px}
.card span{font:600 6.3px/7.4px "Montserrat",Arial,sans-serif;color:#333}
.card--tall{flex-direction:row;padding:6px 8px;gap:14px}
.card--tall .thumb{width:30px;height:46px}
.product .thumb{position:absolute;left:0;background:linear-gradient(120deg,#e9e9e9,#c9c2b4)}
.product-name{position:absolute;left:84px;font:600 9.6px "Montserrat",Arial,sans-serif;color:var(--blue)}
.product-text{position:absolute;left:84px;width:204px;font-size:6.2px;line-height:7.1px;text-align:justify;color:var(--muted)}
.rule{height:1px;background:var(--rule)}
</style>
</head>
<body>
<div class="page-label" style="left:345px">Page 2</div>
<div class="page-label" style="left:863px">Page 3</div>

<main class="spread">
  <!-- Page 2: alarm systems -->
  <div class="photo" role="img" aria-label="Wall-mounted alarm keypad beside a doorway" style="left:245px;top:0;width:256px;height:82px"></div>
  <h1 class="page-title" style="left:25px;top:46px">Alarm Systems</h1>
  <div class="body-text" style="left:25px;top:89px;width:188px">
    <p>A Harrowgate alarm system with its state of the art equipment is the perfect defense for your family and home. With detection devices such as motion detectors, magnetic door sensors and warning devices like siren + strobe combos to alert others of a break in to name a few, it will be everything you need to feel secure.</p>
    <p>With the added option of having your security system monitored, you will always have someone watching over your home, even when the house is vacant.</p>
    <p>Did you know, industry leaders say that burglars are 3 times more likely to to target a home without a security system. This means that simply having a home security system always keeps you safer, even if an alarm is never triggered.</p>
  </div>
  <h2 class="section-head" style="left:245px;top:91px">Home Kits</h2>
  <p class="body-text" style="left:245px;top:114px;width:244px">Standard kits consisting of everything you need to get an alarm up and running. Components such as an Alarm Control Panel, Keypad, 3 motion detectors, and internal siren, an external siren+strobe combo, battery back up incase the power goes out. A great starting platform that can be built on to your needs and requirements.</p>
  <div class="cta" style="left:245px;top:164px;width:242px;height:30px">Request a Security Advisor consultation&nbsp; for all the info.</div>

  <h2 class="upgrades-head" style="left:25px;top:229px">POPULAR UPGRADES</h2>
  <div class="card" style="left:25px;top:253px;width:107px;height:48px"><div class="thumb" role="img" aria-label="OLED keypad"></div><span>OLED Keypad upgrade</span></div>
  <div class="card" style="left:146px;top:253px;width:107px;height:48px"><div class="thumb" role="img" aria-label="Remote key fobs"></div><span>Remote Arm and Disarm</span></div>
  <div class="card" style="left:262px;top:253px;width:107px;height:48px"><div class="thumb" role="img" aria-label="Ceiling motion detector"></div><span>360 degree motion detectors</span></div>
  <div class="card" style="left:382px;top:253px;width:107px;height:48px"><div class="thumb" role="img" aria-label="Magnetic reed switch"></div><span>Door and window magnetic switches</span></div>
  <div class="card" style="left:25px;top:307px;width:107px;height:48px"><div class="thumb" role="img" aria-label="Monitoring communicator"></div><span>Professional Alarm Monitoring</span></div>
  <div class="card" style="left:146px;top:307px;width:107px;height:48px"><div class="thumb" role="img" aria-label="Wall motion detector"></div><span>Motion Detectors' in additional rooms</span></div>
  <div class="card" style="left:262px;top:307px;width:107px;height:48px"><div class="thumb" role="img" aria-label="Roller door switch"></div><span>Roller door magnetic switch</span></div>

  <!-- Page 3: intercom -->
  <div class="photo photo--intercom" role="img" aria-label="Video intercom monitor on a hallway wall" style="left:680px;top:0;width:322px;height:82px"></div>
  <h1 class="page-title" style="left:526px;top:46px">Intercom</h1>
  <div class="body-text" style="left:526px;top:89px;width:288px">
    <p>A Harrowgate Intercom system is a great addition to any home. Giving you the ability to communicate with visitors to your home at your front door or even at your front gate. In conjunction with the use of an electric strike you can hit the door release button on the intercom and let them in from where you stand in the home. Maybe even better still, decide to not let them in.</p>
    <p>With the video intercom option your visitor will be displayed automatically and you can view who it is without them even knowing you are there.</p>
  </div>

  <section class="product" style="left:526px;top:174px;width:290px;height:50px">
    <div class="thumb" role="img" aria-label="Video intercom kit with monitor and door station" style="top:4px;width:72px;height:44px"></div>
    <h3 class="product-name" style="top:-2px">HX Colour Video Intercom</h3>
    <p class="product-text" style="top:11px">Superior quality, touch button control and door release. This sleek glass face 7" screen intercom is just what you need to visually see and communicate with who is at the front gate or door. With the add on addition of a extra monitor makes it perfect for two story homes with the extra station up stairs.</p>
  </section>
  <div class="rule" style="left:526px;top:234px;width:288px"></div>
  <section class="product" style="left:526px;top:246px;width:290px;height:60px">
    <div class="thumb" role="img" aria-label="Glass face monitor and door station" style="top:11px;width:72px;height:36px"></div>
    <h3 class="product-name" style="top:-2px">HV Colour Video Intercom</h3>
    <p class="product-text" style="top:11px">All the smarts built into a compact, modern designed glass face monitor. This unit has touch screen control, inter home communication between monitors and a build in handset for minimal disturbance when required. With maximums of 4 door stations and 8 Monitors, this system is perfect for the homes with multiple entry points and when multiple room monitors are required.</p>
  </section>
  <div class="rule" style="left:526px;top:317px;width:288px"></div>
  <section class="product" style="left:526px;top:326px;width:290px;height:50px">
    <div class="thumb" role="img" aria-label="Audio door station and handset" style="top:0;width:50px;height:50px"></div>
    <h3 class="product-name" style="top:-2px">Audio Only Intercom</h3>
    <p class="product-text" style="top:11px">Whether it's to help fit within the budget, and you just don't have the requirement of having to see who is at the door, this no fuss, single purpose audio only intercom&nbsp; is that handy addition to the living area.</p>
  </section>

  <h2 class="upgrades-head" style="left:840px;top:93px">POPULAR UPGRADES</h2>
  <div class="card card--tall" style="left:840px;top:116px;width:146px;height:62px"><div class="thumb" role="img" aria-label="Stainless door station"></div><span>Upgrade to flush mount stainless steel door station</span></div>
  <div class="card card--tall" style="left:840px;top:185px;width:146px;height:62px"><div class="thumb" role="img" aria-label="Electric strike"></div><span>Extend Intercom wiring to property font gate</span></div>
  <div class="card card--tall" style="left:840px;top:253px;width:146px;height:62px"><div class="thumb" role="img" aria-label="Additional monitor" style="width:48px;height:30px"></div><span>Additional monitor installed. (Video Only)</span></div>
</main>
</body>
</html>
```